Webdesign für Bedrucken Papiertaschen, Schildern etc.
Zielgruppe
Wir bedrucken Papiertaschen, Papierbeutel, Laternen, Aluplaketten, Schilder, etc. und lasern Hundemarken. Zielgruppen von Privat bis Geschäftskunden
Aufgabenstellung
Der Shop sollte ein einfacher und kostengünstiger 'web2print'-shop werden. Wo die Kunden anhand von einem Editor Ihre Logos oder Druckvorlagen selber hochladen und/oder gestalten könne. Bisher haben die Kunden eifach ihre Bidldatei per E-Mail geschickt und wir haben diese dann weiter verarbeit.
Der Shop sollte, wenn möglich, günstig im Unterhalt sein, da wir nicht abschätzen können, wie gut diese laufen wird.
Wir haben wie 3 Bereich: 1. Papierbeutel/Taschen / 2. Stallplaketten (für z.B. Pferdesport) / 3. Diverses (Wie z.B. die Laternen, Schilder, Hundemarken, etc.)
Es würde sich um eine separate Webseite handeln. Daher ist bei Design freie Hand, eifach und klar... auch für nicht so ambitionierte Privatkunden oder kleine Unternehmen.

```html
<!DOCTYPE html>
<html lang="de">
<head>
<meta charset="utf-8">
<title>Taschenwerk – Web2Print</title>
<link rel="stylesheet" href="https://fonts.googleapis.com/css2?family=Inter+Tight:wght@500;600;700&family=Inter:wght@400;500;600&family=JetBrains+Mono:wght@400;500&display=swap">
<style>
:root{
  --red:#e3261b;
  --ink:#111111;
  --muted:#555555;
  --faint:#8a8a8a;
  --line:#e4e4e4;
  --hero-bg:#f6f6f5;
  --white:#ffffff;
  --black:#0b0b0b;
}
*{box-sizing:border-box;margin:0;padding:0}
html,body{width:1200px;height:2859px;overflow:hidden}
body{background:var(--white);color:var(--ink);font-family:"Inter",sans-serif;position:relative}
.abs{position:absolute}
.mono{font-family:"JetBrains Mono",monospace;letter-spacing:.06em;text-transform:uppercase}
.display{font-family:"Inter Tight",sans-serif;font-weight:600;letter-spacing:-.03em}
.topbar{left:0;top:0;width:1200px;height:24px;background:var(--black);color:#ddd;font-size:9.5px;display:flex;align-items:center;justify-content:space-between;padding:0 47px}
.topbar .dot{display:inline-block;width:5px;height:5px;border-radius:50%;background:var(--red);margin-right:6px;vertical-align:middle}
.header{left:0;top:24px;width:1200px;height:68px;background:var(--white);border-bottom:1px solid var(--line);display:flex;align-items:center;padding:0 47px}
.brand{font-family:"Inter Tight",sans-serif;font-weight:700;font-size:17px;letter-spacing:-.02em;display:flex;align-items:center;gap:7px}
.brand .sq{width:12px;height:12px;background:var(--ink)}
.nav{display:flex;gap:24px;margin-left:154px;font-size:12.5px;font-weight:500}
.header .tools{margin-left:auto;display:flex;gap:10px;align-items:center}
.icon-btn{width:30px;height:30px;border:1px solid var(--line);border-radius:50%;display:flex;align-items:center;justify-content:center}
.cart{background:var(--red);color:#fff;border-radius:20px;height:31px;padding:0 14px;display:flex;align-items:center;gap:8px;font-size:12px;font-weight:600}
.cart .n{background:#fff;color:var(--red);width:16px;height:16px;border-radius:50%;font-size:9px;display:flex;align-items:center;justify-content:center}
.hero{left:0;top:92px;width:1200px;height:653px;background:var(--hero-bg);border-bottom:1px solid var(--line)}
.hero h1{left:47px;top:178px;font-size:69px;line-height:68px;font-weight:600}
.hero h1 .red{color:var(--red)}
.hero .lead{left:47px;top:398px;width:430px;font-size:13px;line-height:21px;color:#333}
.btn{display:inline-flex;align-items:center;gap:8px;height:48px;padding:0 24px;border-radius:24px;font-size:13.5px;font-weight:600}
.btn.red{background:var(--red);color:#fff}
.btn.outline{border:1.5px solid var(--ink);background:#fff}
.btn.sm{height:40px;padding:0 19px;font-size:12.5px}
.hero .actions{left:47px;top:484px;display:flex;gap:10px}
.stats{left:47px;top:563px;display:flex;gap:30px}
.stat b{display:block;font-family:"Inter Tight",sans-serif;font-size:27px;font-weight:600;letter-spacing:-.03em}
.stat span{font-size:9.5px;color:var(--muted)}
.hero-photo{left:674px;top:28px;width:479px;height:558px;border-radius:14px;background:linear-gradient(160deg,#6d7682 0%,#9f845e 40%,#b38f64 70%,#7a6a55 100%)}
.price-card{left:650px;top:524px;width:208px;height:87px;background:#fff;border-radius:12px;box-shadow:0 8px 24px rgba(0,0,0,.12);padding:13px 17px}
.price-card .mono{font-size:9px;color:var(--faint)}
.price-card .p{font-family:"Inter Tight",sans-serif;font-weight:600;font-size:23px;letter-spacing:-.02em;margin-top:6px}
.price-card .p small{font-size:10px;font-weight:500;color:var(--muted);letter-spacing:0}
.price-card .d{font-size:9.5px;color:var(--muted);margin-top:3px}
.label{font-size:9.5px;color:var(--muted)}
.h2{font-size:43px;line-height:44px}
.link{font-size:12.5px;font-weight:600;display:flex;gap:8px;align-items:center}
.cards{left:47px;top:901px;display:flex;gap:19px}
.card{width:356px;height:317px;border:1px solid var(--line);border-radius:14px;overflow:hidden;position:relative;background:#fff}
.card .img{height:166px}
.card h3{font-family:"Inter Tight",sans-serif;font-weight:600;font-size:20px;letter-spacing:-.02em;margin:22px 20px 10px}
.card p{font-size:12px;line-height:19px;color:#333;margin:0 20px}
.card .foot{position:absolute;left:20px;right:20px;bottom:20px;display:flex;justify-content:space-between;align-items:center}
.pill{border:1px solid #ccc;border-radius:10px;padding:3px 8px;font-size:9px}
.steps{left:47px;top:1431px;width:1106px;height:180px}
.step{position:absolute;top:0;width:270px}
.circle{width:58px;height:58px;border-radius:50%;border:1.5px solid var(--line);background:#fff;display:flex;align-items:center;justify-content:center;font-family:"Inter Tight",sans-serif;font-weight:600;font-size:17px}
.circle.on{border-color:var(--red);}
.circle.on span{background:var(--red);color:#fff;width:46px;height:46px;border-radius:50%;display:flex;align-items:center;justify-content:center}
.step .pill{display:inline-block;margin-top:13px}
.step h4{font-family:"Inter Tight",sans-serif;font-weight:600;font-size:18px;letter-spacing:-.02em;margin-top:17px}
.step p{font-size:11px;line-height:17px;color:#333;margin-top:8px;width:200px}
.biz{left:47px;top:1645px;width:1106px;height:300px;border:1px solid var(--line);border-radius:18px;background:#fff}
.tiers{position:absolute;left:615px;top:80px;display:grid;grid-template-columns:repeat(3,144px);gap:10px}
.tier{height:64px;border:1px solid var(--line);border-radius:8px;padding:12px 14px}
.tier .mono{font-size:9px;color:var(--faint)}
.tier b{display:block;font-family:"Inter Tight",sans-serif;font-size:19px;font-weight:600;letter-spacing:-.02em;margin-top:4px}
.tier.hot{background:var(--red);border-color:var(--red);color:#fff}
.tier.hot .mono{color:#ffd6d2}
.features{left:0;top:2001px;width:1200px;height:289px;border-top:1px solid var(--line);border-bottom:1px solid var(--line);display:flex;padding:60px 47px 0}
.feature{flex:1;text-align:center;height:168px;border-right:1px solid var(--line);padding:0 40px}
.feature:last-child{border-right:0}
.feature .ic{width:60px;height:60px;border-radius:50%;background:var(--red);margin:0 auto;display:flex;align-items:center;justify-content:center}
.feature h5{font-family:"Inter Tight",sans-serif;font-weight:600;font-size:15px;margin-top:22px}
.feature p{font-size:11px;line-height:17px;color:var(--muted);margin-top:12px}
.reviews{left:47px;top:2335px;display:flex;gap:19px}
.review{width:356px;height:156px;border:1px solid var(--line);border-radius:14px;padding:20px 22px 22px;display:flex;flex-direction:column}
.stars{color:var(--red);font-size:12px;letter-spacing:3px}
.review q{display:block;font-size:15.5px;line-height:21.5px;margin-top:10px;quotes:none}
.review .mono{font-size:9px;color:var(--muted);margin-top:auto}
.footer{left:0;top:2559px;width:1200px;height:300px;background:var(--black);color:#fff}
.footer .about{position:absolute;left:47px;top:40px;width:260px}
.footer .about p{font-size:11px;line-height:17.5px;color:#ddd;margin-top:20px}
.fcol{position:absolute;top:42px}
.fcol h6{font-family:"Inter",sans-serif;font-size:11px;font-weight:600;letter-spacing:.08em;margin-bottom:14px}
.fcol li{list-style:none;font-size:11px;color:#ddd;margin-bottom:7.5px}
.fbar{position:absolute;left:47px;right:47px;top:250px;border-top:1px solid #2a2a2a;padding-top:14px;display:flex;justify-content:space-between;font-size:9.5px;color:#ccc}
.fbar .pay{display:flex;gap:16px}
</style>
</head>
<body>

<div class="abs topbar mono">
  <span><span class="dot"></span>Versand CH ab CHF 9.50 — DE/FR/IT verfügbar</span>
  <span>Druck in 3–5 Werktagen · Lasergravur ab 24 h</span>
  <span>Hilfe? +41 44 000 12 34</span>
</div>

<header class="abs header">
  <div class="brand"><span class="sq"></span>Taschenwerk</div>
  <nav class="nav"><span>Papierbeutel &amp; Taschen</span><span>Stallplaketten</span><span>Hundemarken &amp; Diverses</span><span>Über uns</span><span>Hilfe</span></nav>
  <div class="tools">
    <div class="icon-btn"><svg width="12" height="12" viewBox="0 0 12 12" fill="none" stroke="#111" stroke-width="1.4"><circle cx="5" cy="5" r="3.6"/><path d="M8 8l3 3"/></svg></div>
    <div class="icon-btn"><svg width="12" height="12" viewBox="0 0 12 12" fill="none" stroke="#111" stroke-width="1.3"><circle cx="6" cy="4" r="2.3"/><path d="M1.8 11c.6-2.4 2.2-3.5 4.2-3.5s3.6 1.1 4.2 3.5"/></svg></div>
    <div class="cart"><svg width="12" height="12" viewBox="0 0 12 12" fill="none" stroke="#fff" stroke-width="1.3"><path d="M1 1.5h2l1.2 6h5.6l1-4.3H3.5"/><circle cx="5" cy="10.2" r=".8"/><circle cx="9" cy="10.2" r=".8"/></svg>Warenkorb<span class="n">0</span></div>
  </div>
</header>

<section class="abs hero">
  <h1 class="abs display">Ihr Design.<br><span class="red">Digital</span> bestellt.<br>Präzise produziert.</h1>
  <p class="abs lead">Papierbeutel, Stallplaketten, Hundemarken und mehr — gestalten Sie Ihr Produkt direkt im Browser. Vorlage hochladen, Vorschau prüfen, drucken lassen. Ohne E-Mail-Ping-Pong, ohne Wartezeit.</p>
  <div class="abs actions">
    <span class="btn red"><svg width="13" height="13" viewBox="0 0 13 13" fill="none" stroke="#fff" stroke-width="1.4"><path d="M2 11l1-3 6-6 2 2-6 6z"/></svg>Jetzt gestalten</span>
    <span class="btn outline">Materialmuster bestellen&nbsp;→</span>
  </div>
  <div class="abs stats">
    <div class="stat"><b>3–5</b><span class="mono">Tage Druck</span></div>
    <div class="stat"><b>ab 1</b><span class="mono">Stück Hundemarken</span></div>
    <div class="stat"><b>100%</b><span class="mono">Recyclingpapier</span></div>
    <div class="stat"><b>CH</b><span class="mono">Produktion</span></div>
  </div>
  <div class="abs hero-photo" role="img" aria-label="Foto: bedruckte braune Papiertragetaschen mit weissem Aufdruck"></div>
  <div class="abs price-card">
    <div class="mono">Beispiel · 500 Stk.</div>
    <div class="p">CHF 0.42 <small>/ Stk.</small></div>
    <div class="d">Faltenbeutel braun, 16×26 cm, 1-farbig</div>
  </div>
</section>

<div class="abs label mono" style="left:47px;top:770px">Sortiment</div>
<h2 class="abs display h2" style="left:47px;top:792px">Drei Produktwelten.<br>Ein Workflow.</h2>
<div class="abs link" style="right:47px;top:861px">Alle Produkte ansehen →</div>

<div class="abs cards">
  <div class="card"><div class="img" role="img" aria-label="Foto: Papiertragetasche mit Logo-Aufdruck" style="background:linear-gradient(120deg,#2b3550,#c9a27a 55%,#e7e2dc)"></div>
    <h3>Papierbeutel &amp; Taschen</h3><p>Vom Brötchenbeutel bis zur Tragetasche mit Henkel. 1-farbig bis Vollfarbe.</p>
    <div class="foot"><span class="pill mono">ab 100 Stk.</span><span class="link">Entdecken →</span></div></div>
  <div class="card"><div class="img" role="img" aria-label="Foto: Pferdestall mit Holzboxen" style="background:linear-gradient(180deg,#8a6a4a,#6b3f22 50%,#4a3526)"></div>
    <h3>Stallplaketten</h3><p>Pferdesport, Boxschilder, Boxenbeschriftung. Aluminium oder Kunststoff.</p>
    <div class="foot"><span class="pill mono">ab 1 Stk.</span><span class="link">Entdecken →</span></div></div>
  <div class="card"><div class="img" role="img" aria-label="Foto: Hund mit Hundemarke im Gras" style="background:linear-gradient(180deg,#6f8a3e,#a0693a 55%,#56772c)"></div>
    <h3>Hundemarken &amp; Diverses</h3><p>Lasergravur auf Alu/Edelstahl. Plus Laternen, Schilder und Werbeartikel.</p>
    <div class="foot"><span class="pill mono">ab 1 Stk.</span><span class="link">Entdecken →</span></div></div>
</div>

<div class="abs label mono" style="left:47px;top:1272px">Ablauf</div>
<h2 class="abs display h2" style="left:47px;top:1293px">In vier Schritten<br>zum gedruckten Produkt.</h2>
<span class="abs btn red sm" style="right:47px;top:1339px">Produkt wählen&nbsp;→</span>

<div class="abs steps">
  <svg class="abs" style="left:0;top:0" width="1106" height="58"><line x1="58" y1="29" x2="235" y2="29" stroke="#e3261b" stroke-width="1.2"/><line x1="235" y1="29" x2="1090" y2="29" stroke="#e4e4e4" stroke-width="1.2"/><circle cx="1096" cy="29" r="4.5" fill="none" stroke="#e3261b" stroke-width="1.3"/><path d="M1096 22v14M1089 29h14" stroke="#e3261b" stroke-width="1.1"/></svg>
  <div class="step" style="left:0"><div class="circle on"><span>01</span></div><span class="pill mono">~ 2 Min.</span><h4>Produkt wählen</h4><p>Format, Material, Auflage. Live-Preisberechnung.</p></div>
  <div class="step" style="left:282px"><div class="circle">02</div><span class="pill mono">5–15 Min.</span><h4>Im Editor gestalten</h4><p>Logo hochladen, Text setzen — oder Druckdatei anliefern.</p></div>
  <div class="step" style="left:564px"><div class="circle">03</div><span class="pill mono">~ 1 Min.</span><h4>Bestellung freigeben</h4><p>Vorschau prüfen, bezahlen per PayQuick, Karte oder Rechnung.</p></div>
  <div class="step" style="left:846px"><div class="circle">04</div><span class="pill mono">3–5 Tage</span><h4>Drucken &amp; liefern</h4><p>Produktion in der Schweiz, Versand in 3–5 Werktagen.</p></div>
</div>

<div class="abs biz">
  <div class="abs label mono" style="left:41px;top:38px">Geschäftskunden</div>
  <h2 class="abs display" style="left:41px;top:60px;font-size:37px;line-height:37px">Grossauflagen?<br>Wir offerieren in 24 Std.</h2>
  <p class="abs" style="left:41px;top:151px;width:390px;font-size:12px;line-height:19px;color:#333">Ab 5'000 Beuteln wechseln wir vom Digital- in den Flexodruck. Bis zu 50 % günstiger. Senden Sie uns Format, Auflage und Druckdaten — wir melden uns am nächsten Werktag.</p>
  <div class="abs" style="left:41px;top:225px;display:flex;gap:10px"><span class="btn red sm">Offerte anfordern</span><span class="btn outline sm">Mengenrabatt-Tabelle&nbsp;→</span></div>
  <div class="tiers">
    <div class="tier"><div class="mono">500 Stk.</div><b>CHF 0.42</b></div>
    <div class="tier"><div class="mono">1'000 Stk.</div><b>CHF 0.31</b></div>
    <div class="tier"><div class="mono">2'500 Stk.</div><b>CHF 0.24</b></div>
    <div class="tier hot"><div class="mono">5'000 Stk.</div><b>CHF 0.18</b></div>
    <div class="tier"><div class="mono">10'000 Stk.</div><b>CHF 0.14</b></div>
    <div class="tier"><div class="mono">25'000 Stk.</div><b>Offerte</b></div>
  </div>
</div>

<section class="abs features">
  <div class="feature"><div class="ic"><svg width="22" height="22" viewBox="0 0 22 22" fill="none" stroke="#fff" stroke-width="1.5"><path d="M2 6h11v9H2zM13 9h4l3 3v3h-7"/><circle cx="6" cy="16" r="1.6"/><circle cx="16" cy="16" r="1.6"/></svg></div><h5>Schweizer Produktion</h5><p>Druck und Versand aus 8000 Zürich.</p></div>
  <div class="feature"><div class="ic"><svg width="22" height="22" viewBox="0 0 22 22" fill="none" stroke="#fff" stroke-width="1.5"><path d="M11 2l7 3v5c0 5-3 8-7 10-4-2-7-5-7-10V5z"/><path d="M8 11l2 2 4-4"/></svg></div><h5>Druckvorschau garantiert</h5><p>Was Sie im Editor sehen, kommt so an.</p></div>
  <div class="feature"><div class="ic"><svg width="22" height="22" viewBox="0 0 22 22" fill="none" stroke="#fff" stroke-width="1.5"><path d="M5 18C5 9 10 4 18 4c0 8-5 13-13 14zM5 18l6-6"/></svg></div><h5>Nachhaltigkeit</h5><p>Nachhaltige Materialien als Standard.</p></div>
  <div class="feature"><div class="ic"><svg width="22" height="22" viewBox="0 0 22 22" fill="none" stroke="#fff" stroke-width="1.5"><path d="M12 2L4 13h6l-1 7 8-11h-6z"/></svg></div><h5>Express ab 24 h</h5><p>Hundemarken und Stallplaketten schnell.</p></div>
</section>

<div class="abs reviews">
  <div class="review"><div class="stars">☆☆☆☆☆</div><q>„Endlich kein Datei-Pingpong mehr. Hundemarke samt Gravur in zwei Tagen geliefert."</q><div class="mono">Lena M. · Hundetrainerin, Bern</div></div>
  <div class="review"><div class="stars">☆☆☆☆☆</div><q>„Wir bestellen 2× jährlich 8'000 Bäckerbeutel. Preise stimmen, Termine stimmen."</q><div class="mono">Bäckerei Korn &amp; Kruste, Luzern</div></div>
  <div class="review"><div class="stars">☆☆☆☆☆</div><q>„Stallplaketten für 22 Boxen — Editor war erstaunlich klar. Auch für Nicht-Designer."</q><div class="mono">Reitstall Lindenhof</div></div>
</div>

<footer class="abs footer">
  <div class="about"><div class="brand" style="font-size:15px"><span class="sq" style="background:#fff"></span>Taschenwerk</div>
    <p>Druckerei und Lasergravur aus der Schweiz. Wir bedrucken Papierbeutel, Stallplaketten, Laternen, Schilder und lasern Hundemarken — vom Einzelstück bis zur Grossauflage.</p></div>
  <ul class="fcol" style="left:481px"><h6>PRODUKTE</h6><li>Papierbeutel</li><li>Papiertaschen</li><li>Stallplaketten</li><li>Hundemarken</li><li>Laternen &amp; Schilder</li><li>Aluplaketten</li></ul>
  <ul class="fcol" style="left:719px"><h6>SERVICE</h6><li>Druckvorlagen-Editor</li><li>Druckdaten anliefern</li><li>Materialmuster bestellen</li><li>Mengenrabatte</li><li>Versand &amp; Lieferung</li><li>Hilfe &amp; FAQ</li></ul>
  <ul class="fcol" style="left:956px"><h6>FIRMA</h6><li>Über uns</li><li>Nachhaltigkeit</li><li>Geschäftskunden</li><li>Kontakt</li><li>AGB</li><li>Impressum</li></ul>
  <div class="fbar"><span class="mono" style="text-transform:none;letter-spacing:.03em">© 2026 Taschenwerk · Rindlin Druck AG · CH-8199 Hofbach / Zürich</span>
    <span class="pay"><span>PayQuick</span><span>Cardo</span><span>Globalcard</span><span>Rechnung</span><span>PostKasse</span></span></div>
</footer>

</body>
</html>
```